Harrowgate Supply and Trade, LLC

Would like an e-commerce website started

coldbrook bearings website is a business that is almost exactly like ours...I like how in the front of the website...their lines flash across the bottom...I have attached our line card to add some of ours

we are tolk certified...I would like that to show...... attached logo

also attached our logo

```html
<!DOCTYPE html>
<html lang="en">
<head>
<meta charset="utf-8">
<title>Harrowgate Supply and Trade, LLC</title>
<link href="https://fonts.googleapis.com/css2?family=Open+Sans:wght@400;600;700&display=swap" rel="stylesheet">
<style>
:root{
  --green:#5a9a3b;
  --green-dark:#4d8a30;
  --ink:#2f2f2f;
  --text:#555;
  --line:#e2e2e2;
  --footer:#06080f;
  --white:#fff;
}
*{margin:0;padding:0;box-sizing:border-box}
html,body{width:1200px;height:3317px;overflow:hidden}
body{position:relative;font-family:"Open Sans",sans-serif;color:var(--ink);background:var(--white)}
.abs{position:absolute}
a{color:inherit;text-decoration:none}

/* header */
.site-header{left:0;top:0;width:1200px;height:100px;background:var(--white)}
.brand{left:112px;top:14px;display:flex;align-items:center;gap:10px}
.brand-mark{width:30px;height:58px;background:var(--ink)}
.brand-name{font-size:17px;font-weight:700;line-height:1.15;color:var(--ink);width:190px}
.cert-badge{left:671px;top:9px;width:116px;height:43px;background:#3e3a8f;border-radius:2px}
.call{right:111px;top:18px;display:flex;align-items:center;gap:10px;font-size:15px;color:#444}
.call-icon{width:28px;height:28px;border-radius:50%;background:var(--green);display:flex;align-items:center;justify-content:center}
.call strong{font-size:19px;color:var(--ink);font-weight:700}
.main-nav{top:62px;font-size:14.5px;color:#222}
.main-nav a{position:absolute;white-space:nowrap}
.main-nav .active{color:var(--green)}

/* hero */
.hero{left:0;top:100px;width:1200px;height:643px;background:linear-gradient(180deg,#8a7a66 0%,#a88d6c 25%,#5c5548 55%,#3c3b36 100%)}
.hero-title{left:0;top:330px;width:1200px;text-align:center;color:var(--white);font-size:52px;font-weight:700;line-height:60px}
.btn{display:inline-block;background:var(--green);color:var(--white);font-weight:700;font-size:14px;text-align:center}
.hero-btn{left:533px;top:461px;width:134px;height:40px;line-height:40px}
.dots{left:574px;top:664px;display:flex;gap:8px}
.dots span{width:12px;height:12px;border-radius:50%;background:#bbb}
.dots span.on{background:var(--green)}

/* section headings */
.section-title{left:0;width:1200px;text-align:center;font-size:35px;font-weight:700;color:var(--ink)}
.rule{height:1px;background:var(--line);left:112px;width:977px}

/* clients */
.client{top:900px;width:182px;height:79px;background:var(--white);box-shadow:0 2px 10px rgba(0,0,0,.12);display:flex;align-items:center;justify-content:center;font-size:16px;font-weight:700;color:#666}
.arrow{top:924px}

/* about */
.about-title{left:112px;top:1140px;font-size:34px;font-weight:700;line-height:43px;color:var(--ink)}
.green-bar{height:3px;background:var(--green)}
.about-copy{left:112px;top:1263px;width:470px;font-size:14.5px;line-height:21.5px;color:var(--text);text-align:justify}
.about-btn{left:112px;top:1535px;width:134px;height:39px;line-height:39px}
.about-accent{left:636px;top:1514px;width:470px;height:78px;background:var(--green)}
.about-photo{left:618px;top:1150px;width:470px;height:425px;background:linear-gradient(160deg,#7e8588,#4e5a5e 50%,#6b6f64)}

/* store */
.store-col{top:1835px;height:241px}
.store-col ul{list-style:none}
.store-col li{height:42.9px;font-size:14.5px;color:#333;display:flex;align-items:flex-start;gap:12px;white-space:nowrap}
.store-col li svg{flex:none;margin-top:4px}
.col-sep{top:1835px;width:1px;height:241px;background:var(--line)}

/* location */
.building{left:112px;top:2245px;width:976px;height:376px;background:linear-gradient(180deg,#d9e0e6 0%,#c9d2da 45%,#6c7378 62%,#5e8a3e 85%,#6f8d52 100%)}
.contact-frame{left:618px;top:2530px;width:421px;height:248px;background:var(--white)}
.contact-card{left:626px;top:2538px;width:405px;height:232px;background:var(--green);color:var(--white);font-size:17.5px;line-height:25px;font-style:normal}
.contact-row{position:absolute;left:55px;display:flex;gap:22px}
.contact-row svg{flex:none;margin-top:5px}

/* footer */
.site-footer{left:0;top:2900px;width:1200px;height:417px;background:var(--footer);color:var(--white)}
.footer-brand{left:184px;top:68px;display:flex;align-items:center;gap:12px}
.footer-brand .brand-mark{background:var(--white);width:36px;height:72px}
.footer-brand .brand-name{color:var(--white);font-size:20px;width:200px}
.social{top:209px;width:40px;height:40px;border-radius:50%;background:#1c1e26}
.footer-head{top:78px;font-size:22px;font-weight:700}
.footer-links{top:141px;list-style:none;font-size:14.5px;color:#ddd}
.footer-links li{height:25.8px;display:flex;align-items:center;gap:18px}
.footer-rule{left:112px;top:328px;width:977px;height:1px;background:#2b2d35}
.copyright{left:0;top:361px;width:1200px;text-align:center;font-size:13px;color:#eee}
</style>
</head>
<body>

<header class="site-header abs">
  <div class="brand abs">
    <span class="brand-mark"></span>
    <span class="brand-name">Harrowgate Supply and Trade, LLC</span>
  </div>
  <div class="cert-badge abs" role="img" aria-label="Certification badge"></div>
  <div class="call abs">
    <span class="call-icon"><svg width="14" height="14" viewBox="0 0 24 24"><path fill="#fff" d="M6.6 10.8a15 15 0 0 0 6.6 6.6l2.2-2.2c.3-.3.7-.4 1-.2 1.1.4 2.3.6 3.6.6.6 0 1 .4 1 1V20c0 .6-.4 1-1 1A17 17 0 0 1 3 4c0-.6.4-1 1-1h3.5c.6 0 1 .4 1 1 0 1.3.2 2.5.6 3.6.1.3 0 .7-.2 1z"/></svg></span>
    <span>Call Us Today : <strong>555-214-0830</strong></span>
  </div>
  <nav class="main-nav abs" style="left:0">
    <a class="active" style="left:500px">Home</a>
    <a style="left:574px">Products</a>
    <a style="left:668px">Shop Catalog</a>
    <a style="left:789px">Line Card</a>
    <a style="left:886px">Promotions</a>
    <a style="left:998px">Company Info</a>
  </nav>
</header>

<section class="hero abs" role="img" aria-label="Aerial view of an industrial plant at sunrise"></section>
<h1 class="hero-title abs">INDUSTRIAL PRODUCTS<br>AND SALES</h1>
<a class="btn hero-btn abs">GET STARTED</a>
<div class="dots abs"><span></span><span class="on"></span><span></span></div>

<h2 class="section-title abs" style="top:822px">OUR CLIENTS</h2>
<svg class="arrow abs" style="left:42px" width="16" height="28" viewBox="0 0 16 28"><path d="M13 3 3 14l10 11" fill="none" stroke="#222" stroke-width="2.5"/></svg>
<div class="client abs" style="left:112px">Northmill Gear</div>
<div class="client abs" style="left:310px">Ridgecut</div>
<div class="client abs" style="left:510px">Bedrock Build</div>
<div class="client abs" style="left:707px">Emberflow</div>
<div class="client abs" style="left:906px">Sparkline Weld</div>
<svg class="arrow abs" style="left:1135px" width="16" height="28" viewBox="0 0 16 28"><path d="M3 3l10 11L3 25" fill="none" stroke="#222" stroke-width="2.5"/></svg>

<div class="rule abs" style="top:1074px"></div>

<h2 class="about-title abs">YOUR MATERIAL HANDLING<br>PROBLEM SOLVERS</h2>
<div class="green-bar abs" style="left:112px;top:1238px;width:92px"></div>
<p class="about-copy abs">Lorem ipsum dolor sit amet, consectetur adipiscing elit, sed do eiusmod tempor incididunt ut labore et dolore magna aliqua. Ut enim ad minim veniam, quis nostrud exercitation ullamco laboris nisi ut aliquip ex ea commodo consequat. Duis aute irure dolor in reprehenderit in voluptate velit esse cillum dolore eu fugiat nulla pariatur. Excepteur sint occaecat cupidatat non proident, sunt in culpa qui officia deserunt mollit anim id est laborum. Lorem ipsum dolor sit amet, consectetur adipiscing elit, sed do eiusmod tempor incididunt ut labore et dolore magna aliqua. Ut enim ad minim veniam, quis nostrud exercitation ullamco laboris nisi ut aliquip ex ea commodo consequat. Duis aute irure dolor in reprehenderit in voluptate velit esse cillum dolore eu fugiat nulla pariatur.</p>
<a class="btn about-btn abs">GET STARTED</a>
<div class="about-accent abs"></div>
<div class="about-photo abs" role="img" aria-label="Factory floor with large pipe manufacturing machinery"></div>

<div class="rule abs" style="top:1660px"></div>

<h2 class="section-title abs" style="top:1723px">OUR STORE</h2>
<div class="green-bar abs" style="left:554px;top:1789px;width:92px"></div>

<svg width="0" height="0" style="position:absolute"><defs><symbol id="tick" viewBox="0 0 14 12"><path d="M1 6.5 5 10.5 13 1.5" fill="none" stroke="#5a9a3b" stroke-width="2.6"/></symbol><symbol id="chev" viewBox="0 0 10 10"><path d="M1 1l4 4-4 4M5 1l4 4-4 4" fill="none" stroke="#5a9a3b" stroke-width="1.5"/></symbol></defs></svg>

<div class="store-col abs" style="left:112px"><ul>
  <li><svg width="13" height="11"><use href="#tick"/></svg>Bearing Pullers</li>
  <li><svg width="13" height="11"><use href="#tick"/></svg>Bearings</li>
  <li><svg width="13" height="11"><use href="#tick"/></svg>Belting</li>
  <li><svg width="13" height="11"><use href="#tick"/></svg>Belting-Plastic</li>
  <li><svg width="13" height="11"><use href="#tick"/></svg>Belting-Wire</li>
  <li><svg width="13" height="11"><use href="#tick"/></svg>Bin Boxes</li>
</ul></div>
<div class="col-sep abs" style="left:277px"></div>
<div class="store-col abs" style="left:319px"><ul>
  <li><svg width="13" height="11"><use href="#tick"/></svg>Bin Boxes</li>
  <li><svg width="13" height="11"><use href="#tick"/></svg>Brakes &amp; Cluches</li>
  <li><svg width="13" height="11"><use href="#tick"/></svg>Casteers</li>
  <li><svg width="13" height="11"><use href="#tick"/></svg>Casteers, Rollers,Dollies</li>
  <li><svg width="13" height="11"><use href="#tick"/></svg>Chain &amp; Sprockets</li>
  <li><svg width="13" height="11"><use href="#tick"/></svg>Conveyor Components</li>
</ul></div>
<div class="col-sep abs" style="left:537px"></div>
<div class="store-col abs" style="left:573px"><ul>
  <li><svg width="13" height="11"><use href="#tick"/></svg>Conveyor Pulleys Lagging</li>
  <li><svg width="13" height="11"><use href="#tick"/></svg>Conveyors - Bulk(Drag)</li>
  <li><svg width="13" height="11"><use href="#tick"/></svg>Conveyors - Bulk(Elevator Legs)</li>
  <li><svg width="13" height="11"><use href="#tick"/></svg>Conveyors - Bulk(screw)</li>
  <li><svg width="13" height="11"><use href="#tick"/></svg>Conveyors - Chip Handling</li>
  <li><svg width="13" height="11"><use href="#tick"/></svg>Conveyor Magnetics</li>
</ul></div>
<div class="col-sep abs" style="left:841px"></div>
<div class="store-col abs" style="left:881px"><ul>
  <li><svg width="13" height="11"><use href="#tick"/></svg>Conveyor - Overhead</li>
  <li><svg width="13" height="11"><use href="#tick"/></svg>Conveyors - Package/Unit Handling</li>
  <li><svg width="13" height="11"><use href="#tick"/></svg>Conveyors - Tabletop</li>
  <li><svg width="13" height="11"><use href="#tick"/></svg>Conveyors - Troughed Belt</li>
  <li><svg width="13" height="11"><use href="#tick"/></svg>Conveyors - Vibratory</li>
  <li><svg width="13" height="11"><use href="#tick"/></svg>Couplings</li>
</ul></div>

<div class="rule abs" style="top:2166px"></div>

<div class="building abs" role="img" aria-label="Modern warehouse building with lawn in front"></div>
<div class="contact-frame abs"></div>
<address class="contact-card abs">
  <div class="contact-row" style="top:30px">
    <svg width="12" height="16" viewBox="0 0 12 16"><path fill="#fff" d="M6 0a6 6 0 0 0-6 6c0 4.5 6 10 6 10s6-5.5 6-10a6 6 0 0 0-6-6zm0 8.2A2.2 2.2 0 1 1 6 3.8a2.2 2.2 0 0 1 0 4.4z"/></svg>
    <span>1820 Fenwick Lane Marlow,<br>VA 23990</span>
  </div>
  <div class="contact-row" style="top:107px">
    <svg width="15" height="15" viewBox="0 0 24 24"><path fill="#fff" d="M6.6 10.8a15 15 0 0 0 6.6 6.6l2.2-2.2c.3-.3.7-.4 1-.2 1.1.4 2.3.6 3.6.6.6 0 1 .4 1 1V20c0 .6-.4 1-1 1A17 17 0 0 1 3 4c0-.6.4-1 1-1h3.5c.6 0 1 .4 1 1 0 1.3.2 2.5.6 3.6.1.3 0 .7-.2 1z"/></svg>
    <span>555-214-0830</span>
  </div>
  <div class="contact-row" style="top:132px">
    <svg width="15" height="15" viewBox="0 0 15 15"><rect x="1" y="5" width="13" height="9" fill="#fff"/><rect x="4" y="1" width="7" height="5" fill="none" stroke="#fff" stroke-width="1.5"/></svg>
    <span>555-214-0844</span>
  </div>
  <div class="contact-row" style="top:183px">
    <svg width="16" height="12" viewBox="0 0 16 12"><rect width="16" height="12" fill="#fff"/><path d="M0 0l8 6 8-6" fill="none" stroke="#5a9a3b" stroke-width="1.5"/></svg>
    <span>sales@harrowgatesupply.com</span>
  </div>
</address>

<footer class="site-footer abs">
  <div class="footer-brand abs">
    <span class="brand-mark"></span>
    <span class="brand-name">Harrowgate Supply and Trade, LLC</span>
  </div>
  <a class="social abs" style="left:187px" aria-label="Social profile one"></a>
  <a class="social abs" style="left:239px" aria-label="Social profile two"></a>
  <a class="social abs" style="left:290px" aria-label="Social profile three"></a>

  <h3 class="footer-head abs" style="left:561px">COMPANY</h3>
  <ul class="footer-links abs" style="left:563px">
    <li><svg width="10" height="10"><use href="#chev"/></svg>Home</li>
    <li><svg width="10" height="10"><use href="#chev"/></svg>Products</li>
    <li><svg width="10" height="10"><use href="#chev"/></svg>Shop Catalog</li>
    <li><svg width="10" height="10"><use href="#chev"/></svg>Line Card</li>
    <li><svg width="10" height="10"><use href="#chev"/></svg>Promotions</li>
    <li><svg width="10" height="10"><use href="#chev"/></svg>Company Info</li>
  </ul>

  <h3 class="footer-head abs" style="left:827px">PRODUCTS</h3>
  <ul class="footer-links abs" style="left:829px">
    <li><svg width="10" height="10"><use href="#chev"/></svg>Shop Now</li>
    <li><svg width="10" height="10"><use href="#chev"/></svg>Products</li>
    <li><svg width="10" height="10"><use href="#chev"/></svg>Line Card</li>
    <li><svg width="10" height="10"><use href="#chev"/></svg>Promotions</li>
    <li><svg width="10" height="10"><use href="#chev"/></svg>Terms &amp; Conditions</li>
    <li><svg width="10" height="10"><use href="#chev"/></svg>Privacy policy</li>
  </ul>

  <div class="footer-rule abs"></div>
  <p class="copyright abs">© Copyrights 2024 Company name | All Rights reserved</p>
</footer>

</body>
</html>
```